Business Card Design Project

We need a business card for a new technology services company. We develop software and implement software packages for our business customers and although we will begin with just one or two service offerings, our service offerings will expand over time. Our name comes from the an author, KL Barrow, and his "idea" was that opportunity should be based on ability and achievement, not on social status.

We would like to see a design that is standard in its size and shape, but stands apart in its dramatic color contrasts. The card should not use too many colors - the colors used in the background should highlight the brilliant blues of the logo (see attachment) to dramatic effect. The background should not be white.

If necessary, you can change the color of the words "KL Barrow", but not the word "Idea".

Card size should be U.S. standard 2 inches by 3.5 inches and provide for 1/8 inch bleed area on each side.

We need a design for both sides of the business card, one side communicating the company logo and contact information, the other side being purely graphical, incorporating the logo but no other information.

Contact Information Required:
Kate Brook
KateBrook@klbarrowvista.com
614-387-2259

Target Market(s)

Business executives

Industry/Entity Type

Software

Requirements
Must have
• It must have the full company logo on one side, and at least the graphic element of the logo on the other. Either that or the full logo on both.
Nice to have
• It would be nice to have a design that could work without needing two different textures. For example, it would be nice if the entire card could be shiny, not just parts of the card.

It would also be nice if texture is something we could add later.
Should not have
• The card should not use the color green.

```html
<!DOCTYPE html>
<html lang="en">
<head>
<meta charset="utf-8">
<title>Vista Software – Business Card</title>
<link rel="stylesheet" href="https://fonts.googleapis.com/css2?family=Arimo:wght@400&family=Cinzel:wght@500&display=swap">
<style>
  :root {
    --stage: #e7e4df;
    --card-top: #343437;
    --card-bottom: #1f1f21;
    --brand-blue: #12a4e2;
    --band-blue: #0e9fdc;
    --ink-light: #ffffff;
    --ink-muted: #bfc3c7;
    --divider: rgba(255,255,255,0.7);
  }
  * { box-sizing: border-box; margin: 0; padding: 0; }
  html, body {
    width: 1200px;
    height: 750px;
    overflow: hidden;
    background: var(--stage);
  }
  .sheet {
    position: relative;
    width: 1200px;
    height: 750px;
  }
  .card {
    position: absolute;
    top: 220px;
    width: 540px;
    height: 309px;
    border-radius: 18px;
    overflow: hidden;
    background: linear-gradient(160deg, var(--card-top), var(--card-bottom));
    box-shadow: 0 10px 24px rgba(0,0,0,0.25);
  }
  .card--front { left: 40px; }
  .card--back { left: 620px; }

  .wordmark {
    position: absolute;
    font-family: "Arimo", Arial, sans-serif;
    font-weight: 400;
    letter-spacing: -1px;
    white-space: nowrap;
    line-height: 1;
  }
  .brand-dot {
    position: absolute;
    border-radius: 50%;
    background: var(--brand-blue);
  }

  /* Front */
  .card--front .brand-dot {
    left: 372px;
    top: 36px;
    width: 46px;
    height: 46px;
  }
  .card--front .wordmark {
    left: 58px;
    top: 104px;
    font-size: 42px;
    color: var(--brand-blue);
  }
  .contact-band {
    position: absolute;
    left: 0;
    top: 170px;
    width: 100%;
    height: 58px;
    background: var(--band-blue);
    display: flex;
    align-items: center;
    justify-content: flex-end;
    gap: 14px;
    padding-right: 36px;
    font-family: "Arimo", Arial, sans-serif;
    font-size: 13px;
    color: var(--ink-light);
  }
  .contact-item {
    display: flex;
    align-items: center;
    gap: 6px;
  }
  .contact-item svg { width: 12px; height: 12px; fill: var(--ink-light); }
  .contact-divider {
    width: 1px;
    height: 22px;
    background: var(--divider);
  }
  .holder-name {
    position: absolute;
    top: 246px;
    left: 0;
    width: 100%;
    padding-left: 120px;
    text-align: center;
    font-family: "Cinzel", Georgia, serif;
    font-weight: 500;
    font-size: 19px;
    letter-spacing: 1px;
    color: var(--ink-light);
  }

  /* Back */
  .card--back .brand-dot {
    left: 48px;
    top: 36px;
    width: 120px;
    height: 120px;
    opacity: 0.35;
  }
  .card--back .wordmark {
    right: 40px;
    top: 176px;
    font-size: 54px;
    color: var(--ink-muted);
  }
</style>
</head>
<body>
<main class="sheet">

  <section class="card card--front" aria-label="Business card front">
    <span class="brand-dot" aria-hidden="true"></span>
    <div class="wordmark">Vista Software</div>

    <div class="contact-band">
      <span class="contact-item">
        <svg viewBox="0 0 24 24" aria-hidden="true"><path d="M6.6 10.8a15.1 15.1 0 0 0 6.6 6.6l2.2-2.2c.3-.3.7-.4 1-.2 1.1.4 2.3.6 3.6.6.6 0 1 .4 1 1V20c0 .6-.4 1-1 1A17 17 0 0 1 3 4c0-.6.4-1 1-1h3.5c.6 0 1 .4 1 1 0 1.3.2 2.5.6 3.6.1.3 0 .7-.2 1z"/></svg>
        614-387-2259
      </span>
      <span class="contact-divider" aria-hidden="true"></span>
      <span class="contact-item">
        <svg viewBox="0 0 24 24" aria-hidden="true"><path d="M2 5h20v14H2z M4 7v.5l8 5 8-5V7l-8 5z" fill-rule="evenodd"/></svg>
        KateBrook@klbarrowvista.com
      </span>
    </div>

    <div class="holder-name">KATE BROOK</div>
  </section>

  <section class="card card--back" aria-label="Business card back">
    <span class="brand-dot" aria-hidden="true"></span>
    <div class="wordmark">Vista Software</div>
  </section>

</main>
</body>
</html>
```